Business Card Design

We are looking for a business card designed for our landscaping company. We do landscaping installation & Maintenance Services. We would like to see designs that have basic landscaping in background. We also think it is important to have both of our names and phone numbers on the card. We need something that stands out a little whether it is shape of the card or thickness or design.

Business

Bramblewood Yardworks, bramblewoodyard@mailvista.net, Owen Platt 555-273-9104, Daniel Korbin 555-618-3927

```html
<!DOCTYPE html>
<html lang="en">
<head>
<meta charset="utf-8">
<title>Bramblewood Yardworks — Business Card</title>
<link href="https://fonts.googleapis.com/css2?family=Old+Standard+TT:wght@700&family=Arimo:wght@400&display=swap" rel="stylesheet">
<style>
  :root {
    --page-bg: #e9e6e1;
    --frost-top: #f4f4f2;
    --frost-bottom: #dcdedf;
    --green-light: #5aa64a;
    --green-mid: #3f8a35;
    --green-deep: #2a6625;
    --ink: #111111;
    --ink-soft: #2c2c2c;
    --bar: #141414;
    --trim: #eceae6;
  }
  html, body {
    margin: 0;
    padding: 0;
    width: 1200px;
    height: 970px;
    overflow: hidden;
    background: var(--page-bg);
  }
  .business-card {
    position: absolute;
    left: 100px;
    top: 186px;
    width: 1000px;
    height: 598px;
    box-shadow: 0 18px 40px rgba(0,0,0,0.22);
  }
  .business-card svg { display: block; width: 100%; height: 100%; }
  .company-name {
    font-family: "Old Standard TT", Georgia, serif;
    font-weight: 700;
    font-size: 64px;
    fill: var(--ink);
  }
  .company-email {
    font-family: "Arimo", Arial, sans-serif;
    font-size: 34px;
    fill: var(--ink);
  }
  .partner-name {
    font-family: "Old Standard TT", Georgia, serif;
    font-weight: 700;
    font-size: 41px;
  }
  .partner-phone {
    font-family: "Arimo", Arial, sans-serif;
    font-size: 32px;
  }
  .partner-left { fill: var(--ink-soft); }
  .partner-right { fill: var(--ink); }
</style>
</head>
<body>
  <div class="business-card">
    <svg viewBox="0 0 1070 640" xmlns="http://www.w3.org/2000/svg">
      <defs>
        <linearGradient id="frost" x1="0" y1="0" x2="0" y2="1">
          <stop offset="0" stop-color="var(--frost-top)"/>
          <stop offset="1" stop-color="var(--frost-bottom)"/>
        </linearGradient>
        <linearGradient id="lawn" x1="0" y1="0" x2="1" y2="1">
          <stop offset="0" stop-color="var(--green-mid)"/>
          <stop offset="0.35" stop-color="var(--green-light)"/>
          <stop offset="0.7" stop-color="var(--green-mid)"/>
          <stop offset="1" stop-color="var(--green-deep)"/>
        </linearGradient>
      </defs>

      <rect class="card-face" width="1070" height="640" fill="url(#frost)"/>

      <polygon class="lawn-band" points="0,282 130,355 945,355 1070,282 1070,640 0,640" fill="url(#lawn)"/>
      <polygon class="trim-strip" points="40,290 130,344 945,344 1035,290 945,355 130,355" fill="var(--trim)"/>
      <polygon class="accent-bar" points="40,290 130,320 945,320 1035,290 945,340 130,340" fill="var(--bar)"/>

      <text class="company-name" x="535" y="187" text-anchor="middle">Bramblewood Yardworks</text>
      <text class="company-email" x="535" y="272" text-anchor="middle">bramblewoodyard@mailvista.net</text>

      <line class="partner-divider" x1="535" y1="442" x2="535" y2="570" stroke="var(--bar)" stroke-width="2.5"/>

      <text class="partner-name partner-left" x="427" y="492" text-anchor="end">Owen Platt</text>
      <text class="partner-phone partner-left" x="428" y="539" text-anchor="end">555-273-9104</text>

      <text class="partner-name partner-right" x="630" y="492">Daniel Korbin</text>
      <text class="partner-phone partner-right" x="627" y="539">555-618-3927</text>
    </svg>
  </div>
</body>
</html>
```